Website Revamp: Bravoly.com

Just got a new logo looking for a web design to go with the business. I need the photoshop files and stock photos. No Word Press Please.

```html
<!DOCTYPE html>
<html lang="en">
<head>
<meta charset="utf-8">
<title>Bravoly — Auto Recycling</title>
<link rel="stylesheet" href="https://fonts.googleapis.com/css2?family=Arimo:wght@400;700&family=Open+Sans:wght@400;600;700&family=Montserrat:wght@400;500&display=swap">
<style>
:root{
  --green:#7dc13d;
  --ink:#222222;
  --text:#555555;
  --muted:#8a8a8a;
  --dark:#2a2a2a;
  --yellow:#f6d20b;
  --navy:#0d3c61;
  --light:#f5f5f5;
  --line:#dcdcdc;
  --white:#ffffff;
}
*{box-sizing:border-box;margin:0;padding:0}
html,body{width:1200px;height:4031px;overflow:hidden;background:var(--white)}
body{position:relative;font-family:"Open Sans",sans-serif;color:var(--text)}
.abs{position:absolute}
.heading{font-family:"Arimo",sans-serif;font-weight:700;color:var(--ink);text-transform:uppercase}
.heading .accent{color:var(--green)}

/* header */
.site-header{left:0;top:0;width:1200px;height:103px;background:var(--white);border-top:3px solid var(--green)}
.brand{left:124px;top:30px;display:flex;align-items:center;gap:10px;font-family:"Arimo",sans-serif;font-weight:700;font-size:24px;color:var(--green)}
.brand .dot{width:26px;height:26px;border-radius:50%;background:var(--green)}
.nav{left:0;top:36px;font-family:"Arimo",sans-serif;font-size:17px;color:var(--ink)}
.nav a{position:absolute;white-space:nowrap;color:inherit;text-decoration:none}
.nav a.active{color:var(--green)}
.call-box{left:936px;top:0;width:264px;height:59px}
.call-text{left:980px;top:12px;color:var(--white);font-family:"Arimo",sans-serif;font-size:13px;line-height:19px}
.call-text strong{font-size:17px;font-weight:400}

/* hero */
.hero-photo{left:0;top:103px;width:1200px;height:590px;background:linear-gradient(100deg,#8d8a86 0%,#6f6e6b 30%,#5a5c60 55%,#4c5560 75%,#6a4a45 100%)}
.hero-title{left:108px;top:262px;font-family:"Arimo",sans-serif;font-weight:700;font-size:76px;color:var(--white);letter-spacing:1px}
.hero-sub{left:110px;top:368px;width:650px;font-family:"Arimo",sans-serif;font-weight:700;font-size:23px;line-height:41px;color:var(--white)}
.btn-green{left:105px;top:471px;width:135px;height:40px;border-radius:20px;background:var(--green);color:var(--white);font-weight:700;font-size:14px;display:flex;align-items:center;justify-content:center}
.dots{left:572px;top:662px;display:flex;gap:12px}
.dots span{width:8px;height:8px;border-radius:50%;background:var(--white)}
.dots span.on{background:var(--green)}

/* about */
.about-title{left:111px;top:778px;font-size:38px}
.about-text{left:111px;top:854px;width:562px;font-size:15px;line-height:32.6px;text-align:justify;color:var(--text)}
.btn-dark{left:111px;top:1194px;width:119px;height:40px;border-radius:20px;background:var(--dark);color:var(--white);font-weight:700;font-size:14px;display:flex;align-items:center;justify-content:center}
.about-photo{left:729px;top:805px;width:365px;height:365px;border-radius:50%;background:linear-gradient(180deg,#3d6fb3 0%,#d9a93a 45%,#8a7c64 75%,#c9c9c9 100%)}

/* services */
.services{left:0;top:1322px;width:1200px;height:806px;background:linear-gradient(120deg,#3a3633 0%,#2f2c2a 50%,#3b3835 100%)}
.services-title{left:0;top:1396px;width:1200px;text-align:center;font-size:40px;color:var(--white)}
.services-intro{left:180px;top:1478px;width:840px;text-align:center;font-size:16.5px;line-height:33px;color:#e8e8e8}
.service{width:308px}
.service-photo{position:absolute;left:0;top:0;width:280px;height:202px;border:1px solid #eee}
.service-slant{position:absolute;left:0;top:0;width:308px;height:202px}
.service-icon{position:absolute;left:103px;top:164px;width:84px;height:62px;background:var(--yellow)}
.service-title{position:absolute;left:0;top:252px;width:308px;text-align:center;color:var(--white);font-weight:600;font-size:19px}
.service-text{position:absolute;left:0;top:294px;width:308px;text-align:center;color:#e2e2e2;font-size:15px;line-height:26.5px}
.btn-outline{position:absolute;left:78px;top:394px;width:153px;height:49px;border:2px solid var(--white);border-radius:25px;color:var(--white);font-weight:700;font-size:15px;display:flex;align-items:center;justify-content:center}

/* blog */
.blog-title{left:0;top:2214px;width:1200px;text-align:center;font-size:40px}
.post{background:var(--white);border:1px solid var(--line)}
.post-date{position:absolute;font-size:13px;color:var(--green)}
.post-title{position:absolute;font-family:"Arimo",sans-serif;font-weight:700;font-size:21px;line-height:26px;color:var(--ink)}
.post-text{position:absolute;font-size:11.5px;line-height:27.5px;color:var(--muted)}
.post-more{position:absolute;font-family:"Arimo",sans-serif;font-size:17px;color:var(--green)}

/* contact */
.contact{left:0;top:2968px;width:1200px;height:640px;background:var(--light)}
.contact-title{left:0;top:3036px;width:1200px;text-align:center;font-family:"Arimo",sans-serif;font-weight:700;font-size:29px;color:var(--ink)}
.contact-intro{left:240px;top:3094px;width:720px;text-align:center;font-family:"Arimo",sans-serif;font-size:15px;line-height:27px;color:var(--ink)}
.field{background:var(--white);border:1px solid #cfcfcf;font-family:"Montserrat",sans-serif;font-size:16px;color:#555;padding:14px 22px}
.btn-submit{left:540px;top:3440px;width:120px;height:49px;background:var(--navy);color:var(--white);font-family:"Arimo",sans-serif;font-weight:700;font-size:18px;display:flex;align-items:center;justify-content:center}

/* footer */
.footer-band{left:0;top:3540px;width:1200px;height:491px}
.footer-brand{left:106px;top:3730px;display:flex;align-items:center;gap:10px;font-family:"Arimo",sans-serif;font-weight:700;font-size:26px;color:var(--white)}
.footer-brand .dot{width:28px;height:28px;border-radius:50%;background:var(--white)}
.footer-about{left:109px;top:3804px;width:260px;font-family:"Arimo",sans-serif;font-size:16.5px;line-height:30px;color:var(--white)}
.footer-head{font-family:"Arimo",sans-serif;font-weight:700;font-size:21px;color:var(--white)}
.footer-links{list-style:none;font-family:"Arimo",sans-serif;font-size:16.5px;color:var(--white)}
.footer-links li{height:33.6px;display:flex;align-items:center;gap:10px}
.footer-links svg{width:10px;height:14px}
.social{width:38px;height:38px;border:1.5px solid var(--white);border-radius:50%;display:flex;align-items:center;justify-content:center}
.social svg{width:18px;height:18px}
.footer-rule{left:169px;top:3947px;width:840px;height:1px;background:#777}
.copyright{left:0;top:3984px;width:1200px;text-align:center;font-size:14px;color:var(--white)}
</style>
</head>
<body>

<!-- header -->
<header class="abs site-header">
  <div class="abs brand"><span class="dot"></span>BRAVOLY</div>
  <nav class="abs nav">
    <a class="active" style="left:430px">Home</a>
    <a style="left:514px">About us</a>
    <a style="left:623px">Services</a>
    <a style="left:729px">Blog</a>
    <a style="left:804px">Contact us</a>
  </nav>
</header>
<svg class="abs call-box" viewBox="0 0 264 59"><polygon points="0,0 264,0 264,59 14,59" fill="#7dc13d"/></svg>
<svg class="abs" style="left:943px;top:19px" width="28" height="28" viewBox="0 0 28 28"><circle cx="14" cy="14" r="12.5" fill="none" stroke="#fff" stroke-width="1.5"/><path d="M10 8c-1 1-1.5 2.5-.5 4.5 1 2 3 4.5 5.5 6 2 1 3.5.8 4.5-.2l-2.2-2.2-1.6 1c-1.6-.8-3.3-2.6-4.2-4.2l1-1.6z" fill="#fff"/></svg>
<div class="abs call-text">Call Us<br><strong>555-014-2090</strong></div>

<!-- hero -->
<div class="abs hero-photo" role="img" aria-label="Stacks of scrapped cars piled high in an auto recycling yard under a cloudy sky"></div>
<svg class="abs" style="left:0;top:640px" width="1200" height="80" viewBox="0 0 1200 80"><polygon points="0,50 1200,14 1200,80 0,80" fill="#7dc13d"/><polygon points="0,46 1200,76 1200,80 0,80" fill="#fff"/></svg>
<div class="abs hero-title">BRAVOLY</div>
<div class="abs hero-sub">Neque porro quisquam est qui dolorem ipsum quia dolor sit amet, consectetur, adipisci velit</div>
<div class="abs btn-green">GET STARTED</div>
<div class="abs dots"><span></span><span></span><span class="on"></span></div>

<!-- about -->
<h2 class="abs heading about-title">About <span class="accent">Us</span></h2>
<p class="abs about-text">Lorem ipsum dolor sit amet, consectetur adipiscing elit, sed do eiusmod tempor incididunt ut labore et dolore magna aliqua. Ut enim ad minim veniam, quis nostrud exercitation ullamco laboris nisi ut aliquip ex ea commodo consequat. Duis aute irure dolor in reprehenderit in voluptate velit esse cillum dolore eu fugiat nulla pariatur. Excepteur sint occaecat cupidatat non proident, sunt in culpa qui officia deserunt mollit anim id est laborumAt vero eos et accusamus et iusto odio dignissimos ducimus qui blanditiis praesentium voluptatum deleniti atque corrupti quos dolores et quas molestias excepturi sint occaecati cupiditate non provident, similique sunt in culpa qui officia deserunt mollitia animi,</p>
<div class="abs btn-dark">READ MORE</div>
<div class="abs about-photo" role="img" aria-label="Green recycling emblem framing yellow and blue cars stacked in a scrapyard"></div>

<!-- services -->
<section class="abs services" role="img" aria-label="Dim workshop background with a mechanic at work"></section>
<h2 class="abs heading services-title" style="color:#fff">Our <span class="accent">Services</span></h2>
<p class="abs services-intro">At vero eos et accusamus et iusto odio dignissimos ducimus qui blanditiis praesentium voluptatum deleniti atque corrupti quos dolores et quas molestias excepturi sint occaecati cupiditate non provide.</p>

<div class="abs service" style="left:110px;top:1616px">
  <svg class="service-slant" viewBox="0 0 308 202"><polygon points="270,0 284,0 308,202 294,202" fill="#7dc13d"/></svg>
  <div class="service-photo" role="img" aria-label="Warehouse aisle with shelves of salvaged car parts" style="background:linear-gradient(180deg,#6a4c3a,#a77250 60%,#c9b9a5)"></div>
  <div class="service-icon"><svg width="84" height="62" viewBox="0 0 84 62"><path d="M42 18l-10 16h20zM30 40h24" fill="none" stroke="#222" stroke-width="3" stroke-linejoin="round"/></svg></div>
  <div class="service-title">Neque porro quisquam est</div>
  <div class="service-text">Sed ut perspiciatis unde omnis iste natus error sit voluptatemaccusantium doloremque totam rem.</div>
  <div class="btn-outline">READ MORE</div>
</div>
<div class="abs service" style="left:455px;top:1616px">
  <svg class="service-slant" viewBox="0 0 308 202"><polygon points="270,0 284,0 308,202 294,202" fill="#7dc13d"/></svg>
  <div class="service-photo" role="img" aria-label="Aerial view of rows of parked scrap cars" style="background:linear-gradient(160deg,#3f4a55,#6b7480 50%,#5a5f58)"></div>
  <div class="service-icon"><svg width="84" height="62" viewBox="0 0 84 62"><path d="M32 20h20M35 20v26h14V20M38 24v18M42 24v18M46 24v18M39 20v-3h6v3" fill="none" stroke="#222" stroke-width="2.5"/></svg></div>
  <div class="service-title">Neque porro quisquam est</div>
  <div class="service-text">Sed ut perspiciatis unde omnis iste natus error sit voluptatemaccusantium doloremque totam rem.</div>
  <div class="btn-outline">READ MORE</div>
</div>
<div class="abs service" style="left:799px;top:1616px">
  <svg class="service-slant" viewBox="0 0 308 202"><polygon points="270,0 284,0 308,202 294,202" fill="#7dc13d"/></svg>
  <div class="service-photo" role="img" aria-label="Colourful wrecked cars stacked in a salvage yard" style="background:linear-gradient(180deg,#a8453d,#d8b23c 50%,#b9a58c)"></div>
  <div class="service-icon"><svg width="84" height="62" viewBox="0 0 84 62"><circle cx="42" cy="31" r="13" fill="none" stroke="#222" stroke-width="2.5"/><path d="M42 22v18M35 27h14" stroke="#222" stroke-width="2.5"/></svg></div>
  <div class="service-title">Neque porro quisquam est</div>
  <div class="service-text">Sed ut perspiciatis unde omnis iste natus error sit voluptatemaccusantium doloremque totam rem.</div>
  <div class="btn-outline">READ MORE</div>
</div>

<!-- blog -->
<h2 class="abs heading blog-title">Latest <span class="accent">Blog</span></h2>

<article class="abs post" style="left:114px;top:2333px;width:320px;height:544px">
  <div class="abs" role="img" aria-label="Yellow and blue cars stacked in a scrapyard" style="left:1px;top:1px;width:318px;height:230px;background:linear-gradient(180deg,#4f76b8,#e1b13c 50%,#d3a433 75%,#6b6b6b)"></div>
  <div class="post-date" style="left:32px;top:253px">MAY,2020</div>
  <div class="post-title" style="left:32px;top:282px;width:260px">Sed ut perspiciatis unde omnis iste natus</div>
  <div class="post-text" style="left:32px;top:346px;width:260px">Ut enim ad minima veniaquis nostreierci tationem ullam corporboriosan isi utliquid ex ea commodi eprehenderitq ui in ea voluptmmodate velit .</div>
  <div class="post-more" style="left:34px;top:484px">READ MORE »</div>
</article>

<article class="abs post" style="left:451px;top:2333px;width:643px;height:264px">
  <div class="abs" role="img" aria-label="Close-up of engine gears and machine parts" style="left:3px;top:3px;width:253px;height:258px;background:linear-gradient(135deg,#2f3346,#5c5f72 50%,#8c7c6a)"></div>
  <div class="post-date" style="left:290px;top:30px">MAY,2020</div>
  <div class="post-title" style="left:290px;top:60px;width:330px">Sed ut perspiciatis unde omnis iste natus error</div>
  <div class="post-text" style="left:290px;top:119px;width:330px">Ut enim ad minima veniam, quis nostreierci tationem ullam corporis suscipit laboriosan isi ut aliquid ex ea eprehenderitq utate velit .</div>
  <div class="post-more" style="left:294px;top:218px">READ MORE »</div>
</article>

<article class="abs post" style="left:451px;top:2613px;width:643px;height:264px">
  <div class="abs" role="img" aria-label="Green recycling skips beside trees under a blue sky" style="left:3px;top:3px;width:253px;height:258px;background:linear-gradient(180deg,#6f9ad2,#7f9e5c 45%,#9bbd3c 70%,#7d7d7d)"></div>
  <div class="post-date" style="left:290px;top:30px">MAY,2020</div>
  <div class="post-title" style="left:290px;top:60px;width:330px">Sed ut perspiciatis unde omnis iste natus error</div>
  <div class="post-text" style="left:290px;top:119px;width:330px">Ut enim ad minima veniam, quis nostreierci tationem ullam corporis suscipit laboriosan isi ut aliquid ex ea eprehenderitq utate velit .</div>
  <div class="post-more" style="left:294px;top:218px">READ MORE »</div>
</article>

<!-- contact -->
<section class="abs contact"></section>
<h2 class="abs contact-title">GET IN TOUCH</h2>
<p class="abs contact-intro">Lorem Ipsum is simply dummy text of the printing and typesetting industry. Lorem Ipsum has been the industry's standard</p>
<div class="abs field" style="left:316px;top:3181px;width:285px;height:50px">Name</div>
<div class="abs field" style="left:616px;top:3181px;width:285px;height:50px">Email</div>
<div class="abs field" style="left:316px;top:3242px;width:585px;height:51px">Phone Number</div>
<div class="abs field" style="left:316px;top:3306px;width:585px;height:110px">Message</div>
<div class="abs btn-submit">SUBMIT</div>

<!-- footer -->
<svg class="abs footer-band" viewBox="0 0 1200 491" preserveAspectRatio="none"><polygon points="0,16 560,70 0,90" fill="#7dc13d"/><polygon points="0,90 560,70 1200,60 1200,491 0,491" fill="#2a2a2a"/></svg>
<div class="abs footer-brand"><span class="dot"></span>BRAVOLY</div>
<p class="abs footer-about">Sed ut perspiciatis unde omnis iste natus error sit voluptatem accusantium doloremque.</p>

<div class="abs footer-head" style="left:415px;top:3688px">INFOMATION</div>
<ul class="abs footer-links" style="left:415px;top:3740px">
  <li><svg viewBox="0 0 10 14"><path d="M2 1l6 6-6 6" fill="none" stroke="#fff" stroke-width="1.8"/></svg>Home</li>
  <li><svg viewBox="0 0 10 14"><path d="M2 1l6 6-6 6" fill="none" stroke="#fff" stroke-width="1.8"/></svg>About us</li>
  <li><svg viewBox="0 0 10 14"><path d="M2 1l6 6-6 6" fill="none" stroke="#fff" stroke-width="1.8"/></svg>Services</li>
  <li><svg viewBox="0 0 10 14"><path d="M2 1l6 6-6 6" fill="none" stroke="#fff" stroke-width="1.8"/></svg>Blog</li>
  <li><svg viewBox="0 0 10 14"><path d="M2 1l6 6-6 6" fill="none" stroke="#fff" stroke-width="1.8"/></svg>Contact us</li>
</ul>

<div class="abs footer-head" style="left:648px;top:3688px">HELPFUL LINKS</div>
<ul class="abs footer-links" style="left:648px;top:3740px">
  <li><svg viewBox="0 0 10 14"><path d="M2 1l6 6-6 6" fill="none" stroke="#fff" stroke-width="1.8"/></svg>Services</li>
  <li><svg viewBox="0 0 10 14"><path d="M2 1l6 6-6 6" fill="none" stroke="#fff" stroke-width="1.8"/></svg>Support</li>
  <li><svg viewBox="0 0 10 14"><path d="M2 1l6 6-6 6" fill="none" stroke="#fff" stroke-width="1.8"/></svg>Terms &amp; conditions</li>
  <li><svg viewBox="0 0 10 14"><path d="M2 1l6 6-6 6" fill="none" stroke="#fff" stroke-width="1.8"/></svg>Privacy policy</li>
</ul>

<div class="abs footer-head" style="left:914px;top:3688px">FOLLOW US</div>
<div class="abs social" style="left:915px;top:3742px" aria-label="Share">
  <svg viewBox="0 0 18 18"><circle cx="13" cy="4" r="2.2" fill="#fff"/><circle cx="5" cy="9" r="2.2" fill="#fff"/><circle cx="13" cy="14" r="2.2" fill="#fff"/><path d="M13 4L5 9l8 5" fill="none" stroke="#fff" stroke-width="1.4"/></svg>
</div>
<div class="abs social" style="left:968px;top:3742px" aria-label="Email">
  <svg viewBox="0 0 18 18"><rect x="2" y="4" width="14" height="10" rx="1" fill="none" stroke="#fff" stroke-width="1.5"/><path d="M2.5 4.5L9 10l6.5-5.5" fill="none" stroke="#fff" stroke-width="1.5"/></svg>
</div>
<div class="abs social" style="left:1026px;top:3742px" aria-label="Website">
  <svg viewBox="0 0 18 18"><circle cx="9" cy="9" r="7" fill="none" stroke="#fff" stroke-width="1.5"/><ellipse cx="9" cy="9" rx="3" ry="7" fill="none" stroke="#fff" stroke-width="1.3"/><path d="M2 9h14" stroke="#fff" stroke-width="1.3"/></svg>
</div>

<div class="abs footer-rule"></div>
<p class="abs copyright">© 2020 All Rights Reserved | Privacy Policy | Terms and Conditions</p>

</body>
</html>
```